Product Label & Logo for New Supplement

Your design will automatically be eliminated if you do NOT read this brief, because the description tells you about the brand you will be creating an identity for.Attached is the current label for the product. It is boring and doesn’t tell a story.We need you to unleash creative work to help patients with chronic pain diseases - like Multiple Sclerosis, Chronic Fatigue Syndrome, Lupus, and Fibromyalgia - no longer be defined by their disease. Velbrin Core is a new supplement developed by a neurologist to help patients with chronic pain feel better and have better days. It increases energy and stamina, saving the patient from having to take upwards of 40 different supplements.The label and logo need to convey that this supplement will give hurting patients new life.
Target Market(s)
People with fatigue, pain and inflammation
Industry/Entity Type
Supplement
Requirements
Must have
- Gender neutral, eye catching, all the ingredients listed in addition to logo design
Nice to have
- Custom logo, no generic fonts for name brand

```html
<!DOCTYPE html>
<html lang="en">
<head>
<meta charset="utf-8">
<title>Velbrin Core – Supplement Label</title>
<link href="https://fonts.googleapis.com/css2?family=Oswald:wght@500&display=swap" rel="stylesheet">
<style>
  :root {
    --stage: #1e1e1e;
    --ink: #3d1580;
    --band: rgba(255, 255, 255, 0.55);
    --blue-deep: #2a46c8;
    --blue-mid: #4f7fe6;
    --blue-light: #9cc4f6;
    --violet: #8a3be0;
    --violet-light: #c49af0;
    --violet-deep: #5518b0;
    --glow: #ffffff;
  }
  * { box-sizing: border-box; margin: 0; padding: 0; }
  html, body {
    width: 1200px;
    height: 787px;
    overflow: hidden;
    background: var(--stage);
  }
  .label {
    position: absolute;
    left: 285px;
    top: 0;
    width: 630px;
    height: 787px;
    overflow: hidden;
    font-family: "Oswald", "Arial Narrow", sans-serif;
    font-weight: 500;
    color: var(--ink);
  }
  .label__art {
    position: absolute;
    inset: 0;
    background:
      radial-gradient(ellipse 30% 22% at 72% 60%, var(--glow) 0%, rgba(255,255,255,0.6) 40%, rgba(255,255,255,0) 100%),
      radial-gradient(ellipse 26% 18% at 85% 38%, rgba(255,255,255,0.75) 0%, rgba(255,255,255,0) 100%),
      linear-gradient(112deg, rgba(255,255,255,0) 30%, rgba(196,154,240,0.55) 40%, rgba(232,200,255,0.7) 46%, rgba(160,90,230,0.6) 54%, rgba(255,255,255,0) 64%),
      radial-gradient(ellipse 40% 30% at 10% 70%, rgba(120, 40, 210, 0.9) 0%, rgba(120,40,210,0) 100%),
      radial-gradient(ellipse 40% 26% at 75% 22%, rgba(156,196,246,0.9) 0%, rgba(156,196,246,0) 100%),
      linear-gradient(180deg, var(--blue-deep) 0%, var(--blue-mid) 18%, var(--blue-light) 34%, var(--violet) 58%, var(--violet-light) 72%, var(--violet-deep) 100%);
  }
  .band {
    position: absolute;
    left: 0;
    width: 100%;
    background: var(--band);
  }
  .band--top { top: 67px; height: 103px; }
  .band--bottom { top: 586px; height: 94px; }
  .brand-mark {
    position: absolute;
    left: 40px;
    top: 96px;
    display: flex;
    align-items: center;
    gap: 10px;
    font-size: 30px;
    line-height: 44px;
    text-transform: uppercase;
  }
  .brand-mark__dot {
    width: 26px;
    height: 26px;
    border-radius: 50%;
    background: var(--ink);
  }
  .claims {
    position: absolute;
    left: 391px;
    top: 80px;
    list-style: none;
    font-size: 21px;
    line-height: 30px;
    text-transform: uppercase;
    letter-spacing: -0.3px;
  }
  .wordmark {
    position: absolute;
    left: 34px;
    top: 310px;
    font-size: 102px;
    font-weight: 500;
    line-height: 1.2;
    letter-spacing: 7px;
    white-space: nowrap;
  }
  .format {
    position: absolute;
    left: 34px;
    top: 596px;
    font-size: 24px;
    line-height: 36px;
    text-transform: uppercase;
  }
  .count {
    position: absolute;
    left: 461px;
    top: 613px;
    font-size: 24px;
    line-height: 34px;
    text-transform: uppercase;
  }
</style>
</head>
<body>
  <main class="label">
    <div class="label__art" role="img" aria-label="Illustration of a glowing purple and blue DNA double helix with floating particles"></div>
    <div class="band band--top"></div>
    <div class="band band--bottom"></div>

    <div class="brand-mark"><span class="brand-mark__dot"></span><span>Velbrin Core</span></div>

    <ul class="claims">
      <li>Promotes Energy</li>
      <li>Decreases Pain</li>
      <li>Relieves Inflammation</li>
    </ul>

    <h1 class="wordmark">Velbrin Core</h1>

    <p class="format">Dietary<br>Supplement</p>
    <p class="count">60 Tablets</p>
  </main>
</body>
</html>
```